Flyer Design for Coastal Guild of Reflective Counsellors and Psychotherapists (CGRCP)

We need a new flyer designed for CGRCP. We want to attract new members @ a tradeshow. Counsellors and Psychotherapists looking for a professional association with which to align themselves where they feel @ home because they share similar values.We would like to use the colours and leaves from our website which is www.cgrcp-guild.org if possible or similar colours and the photo of the tree in bloom from Facebook "stillwaterandmindwork". As well as our logo (www.cgrcp-guild.org), the TRELMO (www.trelmo-hub.org) logo as well somewhere in the bottom corner the Harbour Circle logo (www.harbourcirclenet.org).
Updates

Target Market(s)

Psychotherapists and Counsellors

Industry/Entity Type

Mental Health

Colors
876aae
b7a5cd
e4daeb
cadf82
abd036
9bcb3b

Requirements
Must have
• Logo
Nice to have
• Warm inviting photo of lotus flower
Should not have
• No monks

```html
<!DOCTYPE html>
<html lang="en">
<head>
<meta charset="utf-8">
<title>CGRCP Flyer</title>
<link href="https://fonts.googleapis.com/css2?family=Source+Sans+3:wght@300;400;600&display=swap" rel="stylesheet">
<style>
  :root {
    --bg: #eeeeee;
    --paper: #ffffff;
    --lavender: #b7a5cd;
    --lavender-text: #a18fbf;
    --purple: #876aae;
    --pale: #e4daeb;
    --ink: #222222;
    --rule: #9a9aa6;
    --leaf-green: #4f9a78;
    --pond: #6b5585;
    --trelmo: #1f3b72;
  }
  * { margin: 0; padding: 0; box-sizing: border-box; }
  html, body { width: 1200px; height: 900px; overflow: hidden; }
  body {
    background: var(--bg);
    font-family: "Source Sans 3", "Helvetica Neue", Arial, sans-serif;
    position: relative;
  }
  .page {
    position: absolute;
    top: 90px;
    width: 517px;
    height: 732px;
    overflow: hidden;
    background: var(--paper);
  }
  .page--front { left: 69px; }
  .page--back { left: 611px; }

  /* Front */
  .cover-photo {
    position: absolute; inset: 0;
    background:
      radial-gradient(ellipse 230px 150px at 52% 73%, #f6eef6 0%, #e9d9ea 45%, rgba(200,170,210,0) 100%),
      radial-gradient(ellipse 60px 30px at 52% 68%, #f2e27a 0%, rgba(242,226,122,0) 100%),
      linear-gradient(180deg, #5fa287 0%, #548f7a 25%, #6f6690 45%, #5a4876 65%, #7e6794 85%, #6a5580 100%);
  }
  .cover-band {
    position: absolute; left: 0; right: 0; top: 37px; height: 36px;
    background: var(--lavender);
    color: #fff; font-weight: 600; font-size: 13.5px;
    display: flex; align-items: center; padding-left: 35px;
  }
  .cover-name {
    position: absolute; left: 0; right: 0; top: 112px;
    text-align: center; color: #fff; font-weight: 300; font-size: 46px; letter-spacing: 1px;
  }
  .cover-mark {
    position: absolute; left: 220px; top: 192px; width: 78px; height: 78px;
    border: 3px solid #fff; border-radius: 50%;
  }
  .partner-box {
    position: absolute; left: 414px; top: 638px; width: 103px; height: 62px;
    background: #fff; display: flex; align-items: center; justify-content: center;
    color: var(--trelmo); font-size: 16px; font-weight: 400; letter-spacing: 1px;
  }

  /* Back */
  .leaves {
    position: absolute;
    background: linear-gradient(135deg, var(--pale) 0%, rgba(228,218,235,0.35) 100%);
    border-radius: 50% 0 50% 0;
    opacity: 0.8;
  }
  .leaves--top-left { left: -10px; top: 0; width: 95px; height: 200px; }
  .leaves--top { left: 195px; top: -10px; width: 95px; height: 50px; }
  .leaves--bottom-right { right: -10px; top: 500px; width: 55px; height: 145px; }

  .brand-name {
    position: absolute; left: 74px; top: 46px;
    font-size: 28px; font-weight: 300; color: var(--ink); letter-spacing: 0.5px;
  }
  .brand-mark {
    position: absolute; left: 96px; top: 88px; width: 66px; height: 66px;
    border: 3px solid var(--ink); border-radius: 50%;
  }
  .tagline {
    position: absolute; left: 260px; top: 46px;
    font-size: 21px; font-weight: 300; line-height: 28px; color: var(--lavender-text);
    text-transform: uppercase;
  }
  .col { position: absolute; top: 184px; }
  .col--left { left: 29px; width: 192px; }
  .col--right { left: 260px; width: 230px; }
  .col h2 {
    font-size: 22px; font-weight: 300; color: var(--ink); margin-bottom: 12px;
  }
  .col p {
    font-size: 11.6px; line-height: 14.2px; color: var(--lavender-text);
    text-align: justify; hyphens: auto;
  }
  .col--left p { text-align: left; }
  .col .gap { margin-bottom: 14px; }
  .col h2.values { margin-top: 12px; }
  .goals p.tight { margin-bottom: 0; }

  .footer-rule {
    position: absolute; left: 29px; width: 461px; top: 659px;
    border-top: 1px solid var(--rule);
  }
  .contact {
    position: absolute; right: 27px; top: 667px; text-align: right;
    font-size: 11.5px; line-height: 14px; color: var(--ink);
  }
</style>
</head>
<body>

<section class="page page--front">
  <div class="cover-photo" role="img" aria-label="Photograph of a pale pink water lily with yellow centre floating among green lily pads, reflected in the pond"></div>
  <div class="cover-band">Coastal Guild of Reflective Counsellors and Psychotherapists</div>
  <div class="cover-name">CGRCP</div>
  <div class="cover-mark" aria-hidden="true"></div>
  <div class="partner-box">TRELMO</div>
</section>

<section class="page page--back">
  <div class="leaves leaves--top-left" role="img" aria-label="Faint lavender leaves decoration"></div>
  <div class="leaves leaves--top" role="img" aria-label="Faint lavender leaf decoration"></div>
  <div class="leaves leaves--bottom-right" role="img" aria-label="Faint lavender leaves decoration"></div>

  <div class="brand-name">CGRCP</div>
  <div class="brand-mark" aria-hidden="true"></div>

  <h1 class="tagline">Enriching the lives<br>of counsellors and<br>psychotherapists<br>with Buddhism</h1>

  <div class="col col--left">
    <h2>Our Purpose</h2>
    <p>The purpose of The Coastal Guild of Reflective Counsellors and Psychotherapists (CGRCP), a TRELMO Member Association, is to use the whole philosophy; teachings and practices of Buddhism (the dhamma), to provide innovative educational experiences that inform and guide our mental health professionals in their work and in their lives, and to provide an organisation that supports the development of a unique community of Buddhist informed therapists.</p>
    <h2 class="values">Some of Our Values</h2>
    <p class="gap">We care about therapists</p>
    <p class="gap">We strive to be of service to our members and all those we come into contact with humility, fairness, patience and compassion</p>
    <p>We value the ongoing need for education for therapists but we also value the balance between the mind, the body and the spirit, knowing that all those need to be nourished</p>
  </div>

  <div class="col col--right goals">
    <h2>Our Goals</h2>
    <p class="gap">Provide a dynamic organisation that stays attuned to the changes in Buddhism as it is expressed in the West.</p>
    <p class="gap">Provide accreditation practices that will support the highest quality practice in Buddhist Counselling and Psychotherapy.</p>
    <p class="tight">Provide a philosophical base, standards and ethics for the practice of Buddhist Counselling and Psychotherapy.</p>
    <p class="tight">Explore and discuss dhamma and how it can improve the quality of a therapist’s whole life.</p>
    <p class="tight">Maintain unique professional development of its members, as well as provide a warm and supportive community of mental health practitioners.</p>
    <p class="tight">Develop a professional organisational structure that supports the practice of Buddhist Counselling and Psychotherapy;</p>
    <p class="tight">Provide an innovative education, training and research in Buddhist Counselling and Psychotherapy;</p>
    <p class="tight">To promote Buddhist Counselling and Psychotherapy in the community;</p>
    <p class="tight">And work collaboratively and beneficially with other National and International Buddhist Counselling and Psychotherapy Organisations.</p>
  </div>

  <div class="footer-rule"></div>
  <div class="contact">
    www.stillwaterandmindwork.org<br>
    info@stillwaterandmindwork.org
  </div>
</section>

</body>
</html>
```